Maple Roster Business Card for recruitment company

We are looking for a Business Card Design that incorporates our personal details and our busines name and logo. We are a specialized search consultancy that recruit Property and Construction professionals.
We would like a business card that stands out and is appealing to the Construction and Property industry as well.

Target Market(s)

people in the construction and property industry

Contact Information for Business Card

Business Name and logo

Font styles to use
Serif

Colors
0094D4
00A9DD
6FCCEA
C7EBF8
E9F6FB

Requirements
Must have
• Business name and logo as well as contact details
Should not have
• No photos of us please

```html
<!DOCTYPE html>
<html lang="en">
<head>
<meta charset="utf-8">
<title>Maple Roster – Business Card</title>
<link rel="stylesheet" href="https://fonts.googleapis.com/css2?family=Questrial&family=Montserrat:wght@700&display=swap">
<style>
  :root {
    --backdrop: #1f2021;
    --navy: #07344a;
    --slate: #343d3d;
    --slate-deep: #283031;
    --stripe-light: #ffffff;
    --stripe-shade: #d9d9d9;
    --ink: #ffffff;
  }
  * { margin: 0; padding: 0; box-sizing: border-box; }
  html, body {
    width: 1200px; height: 732px; overflow: hidden;
    background: var(--backdrop);
  }
  .canvas { position: relative; width: 1200px; height: 732px; }
  .card {
    position: absolute; top: 242px;
    width: 436px; height: 248px; overflow: hidden;
    box-shadow: 0 6px 14px rgba(0,0,0,0.55);
  }
  .card--front { left: 144px; }
  .card--back { left: 621px; }
  .card__shapes { position: absolute; inset: 0; width: 100%; height: 100%; }
  .brand-name {
    position: absolute; left: 16px; top: 13px;
    font-family: "Questrial", sans-serif;
    font-size: 28px; letter-spacing: 0.5px;
    color: var(--ink); text-transform: uppercase; line-height: 1;
  }
  .contact {
    position: absolute; right: 18px; top: 145px;
    text-align: right; color: var(--ink);
    font-family: "Questrial", sans-serif;
  }
  .contact__name {
    font-family: "Montserrat", sans-serif;
    font-weight: 700; font-size: 15.5px; line-height: 19px;
  }
  .contact__role { font-size: 12px; line-height: 14px; }
  .contact__lines { margin-top: 14px; font-size: 12px; line-height: 14px; }
  .contact__label {
    font-family: "Montserrat", sans-serif; font-weight: 700;
    font-size: 10.5px; margin-right: 8px;
  }
  .back-brand {
    position: absolute; left: 16px; top: 172px;
    display: flex; align-items: center; gap: 10px;
  }
  .back-brand__dot {
    width: 16px; height: 16px; border-radius: 50%;
    background: var(--ink);
  }
  .back-brand__name {
    font-family: "Questrial", sans-serif;
    font-size: 22px; color: var(--ink); text-transform: uppercase;
    letter-spacing: 0.5px;
  }
</style>
</head>
<body>
<main class="canvas">
  <section class="card card--front">
    <svg class="card__shapes" viewBox="0 0 436 248" preserveAspectRatio="none" aria-hidden="true">
      <defs>
        <linearGradient id="stripeFront" x1="0" y1="0" x2="0" y2="1">
          <stop offset="0" stop-color="var(--stripe-light)"/>
          <stop offset="1" stop-color="#eeeeee"/>
        </linearGradient>
      </defs>
      <polygon points="0,0 286,0 101,248 0,248" fill="var(--navy)"/>
      <polygon points="286,0 328,0 109,248 101,248" fill="url(#stripeFront)"/>
      <polygon points="328,0 436,0 436,248 109,248" fill="var(--slate)"/>
    </svg>
    <div class="brand-name">Maple Roster</div>
    <div class="contact">
      <div class="contact__name">Claire Henley</div>
      <div class="contact__role">Director &nbsp;|&nbsp; Senior Search Consultant</div>
      <div class="contact__lines">
        <div><span class="contact__label">T:</span> +64 21 555 0142</div>
        <div><span class="contact__label">E:</span> claire@mapleroster.nz</div>
        <div><span class="contact__label">W:</span>www.mapleroster.nz</div>
      </div>
    </div>
  </section>

  <section class="card card--back">
    <svg class="card__shapes" viewBox="0 0 436 248" preserveAspectRatio="none" aria-hidden="true">
      <defs>
        <linearGradient id="slateBack" x1="0" y1="0" x2="1" y2="0">
          <stop offset="0" stop-color="var(--slate)"/>
          <stop offset="1" stop-color="var(--slate-deep)"/>
        </linearGradient>
        <linearGradient id="stripeBack" x1="0" y1="0" x2="0" y2="1">
          <stop offset="0" stop-color="var(--stripe-light)"/>
          <stop offset="1" stop-color="var(--stripe-shade)"/>
        </linearGradient>
      </defs>
      <polygon points="0,0 108,0 326,248 0,248" fill="var(--navy)"/>
      <polygon points="108,0 150,0 335,248 326,248" fill="url(#stripeBack)"/>
      <polygon points="150,0 436,0 436,248 335,248" fill="url(#slateBack)"/>
    </svg>
    <div class="back-brand">
      <span class="back-brand__dot"></span>
      <span class="back-brand__name">Maple Roster</span>
    </div>
  </section>
</main>
</body>
</html>
```